We’re a real estate firm that has landed a big builder in a neighboring state. Our branding needs...

We are a real estate firm who represents various builders along with doing resale here in Oregon. Our firm is growing to represent a big builder in Washington State and we’ll have another 40 brokers on our team. We need rebranding. As in, a new logo ( the house logo we have now looks cartoonish, hate it). We need new cards, something to really stand out. I’ve been thinking of using those NFC cards from ZEP or the ones with the seam color. I likely want two or three designs, a darker (as in a background color of black or grey) , a light one ( again I mean background color) and a credit card style (either plastic w an embossed name/number on front, or metal ). I’m thinking dark background for cc, or silver if it’s metal. That’s my thoughts, but you are the artists, so maybe you have an idea I haven’t considered. Our colors were black and red, but we don’t have to stick to that. Just nothing too busy. Oh, and we are typically representing the local, higher quality builders in our area (just below custom), but not national. Subdivisions are near the Kell Varney, Brisco, and Thornfield Crest sites. We are super excited, but without a lot of time to change the “look” of our brokerage. So I’ll be deciding and moving forward within 24 hours tops. Our name is Real Estate Summit Alliance ( we cant change the name because of timeline and business license) Thank you!

Industry/Entity Type

Real Estate

Contact Information for Business Card

The usual. Name of firm. Name of cardholder. Contact info.

Font styles to use
Serif
Sans Serif

Colors

Designer to choose colors to be used in the design.

Requirements
Must have
• A sleek or simple look. I included photos of cards with stylistic attributes we like. Thank you
Nice to have
• We really like the black backgrounds. With foil or embossed detail. We also like the black on black. Matte black card with raised shiny black detail. But still eye catching.
Should not have
• No ornate or busy looking style. We don’t want anything cluttered.

```html
<!DOCTYPE html>
<html lang="en">
<head>
<meta charset="utf-8">
<title>Real Estate Summit Alliance – Business Cards</title>
<link rel="stylesheet" href="https://fonts.googleapis.com/css2?family=Arimo:wght@400;700&family=Cinzel:wght@400&display=swap">
<style>
  :root {
    --stage: #2b2b2b;
    --stage-deep: #1f1f1f;
    --card: #121212;
    --card-edge: #1a1a1a;
    --emboss: #262626;
    --brand-blue: #1f6fd1;
    --text-light: #e6e6e6;
    --text-muted: #9a9a9a;
    --divider: #4a4a4a;
  }
  * { box-sizing: border-box; margin: 0; padding: 0; }
  html, body { width: 1200px; height: 900px; overflow: hidden; }
  body {
    background: radial-gradient(ellipse at 50% 40%, var(--stage) 0%, var(--stage-deep) 100%);
    position: relative;
    font-family: "Arimo", Arial, sans-serif;
  }
  .card {
    position: absolute;
    left: 340px;
    width: 520px;
    height: 297px;
    background: linear-gradient(160deg, var(--card-edge) 0%, var(--card) 60%);
    box-shadow: 0 10px 30px rgba(0,0,0,0.5);
  }
  .card--back { top: 110px; display: flex; align-items: center; justify-content: center; }
  .card--front { top: 480px; }

  .back-name {
    font-family: "Cinzel", Georgia, serif;
    font-weight: 400;
    font-size: 22px;
    letter-spacing: 1px;
    color: var(--emboss);
    white-space: nowrap;
  }

  .firm-name {
    position: absolute;
    left: 70px;
    top: 22px;
    height: 253px;
    writing-mode: vertical-rl;
    transform: rotate(180deg);
    display: flex;
    align-items: center;
    justify-content: center;
    gap: 10px;
    font-family: "Cinzel", Georgia, serif;
    font-weight: 400;
    font-size: 13px;
    letter-spacing: 1px;
    color: var(--brand-blue);
    white-space: nowrap;
  }
  .firm-name__square {
    width: 10px;
    height: 10px;
    background: var(--brand-blue);
    flex: none;
  }

  .divider {
    position: absolute;
    left: 170px;
    top: 60px;
    width: 1px;
    height: 90px;
    background: var(--divider);
  }

  .details {
    position: absolute;
    left: 196px;
    top: 44px;
    color: var(--text-light);
  }
  .details__name {
    font-family: "Cinzel", Georgia, serif;
    font-weight: 400;
    font-size: 24px;
    letter-spacing: 1px;
    color: var(--brand-blue);
    line-height: 1;
  }
  .details__title {
    font-size: 13px;
    color: var(--text-muted);
    margin-top: 4px;
  }
  .contact-list { list-style: none; margin-top: 14px; }
  .contact-list li {
    display: flex;
    align-items: center;
    gap: 8px;
    font-size: 15px;
    line-height: 20px;
  }
  .contact-list svg { width: 11px; height: 11px; fill: var(--brand-blue); flex: none; }
  .address {
    font-size: 15px;
    line-height: 19px;
    margin-top: 14px;
    font-style: normal;
  }
</style>
</head>
<body>

  <section class="card card--back" aria-label="Card back">
    <span class="back-name">Real Estate Summit Alliance</span>
  </section>

  <section class="card card--front" aria-label="Card front">
    <div class="firm-name">
      <span class="firm-name__square" aria-hidden="true"></span>
      <span>Real Estate Summit Alliance</span>
    </div>

    <div class="divider"></div>

    <div class="details">
      <h1 class="details__name">JOHN SMITH</h1>
      <p class="details__title">Managing Director</p>
      <ul class="contact-list">
        <li>
          <svg viewBox="0 0 12 12" aria-hidden="true"><path d="M2 1h3l1 3-1.5 1a6 6 0 0 0 2.5 2.5L8 6l3 1v3a1 1 0 0 1-1 1A9 9 0 0 1 1 2a1 1 0 0 1 1-1z"/></svg>
          044-123 456 789
        </li>
        <li>
          <svg viewBox="0 0 12 12" aria-hidden="true"><path d="M3 0h6a1 1 0 0 1 1 1v10a1 1 0 0 1-1 1H3a1 1 0 0 1-1-1V1a1 1 0 0 1 1-1zm0 2v7h6V2z"/></svg>
          044-123 456 789
        </li>
        <li>
          <svg viewBox="0 0 12 12" aria-hidden="true"><path d="M0 2h12v8H0zm1 1v.4l5 3.2 5-3.2V3z"/></svg>
          info@webname.com
        </li>
        <li>
          <svg viewBox="0 0 12 12" aria-hidden="true"><circle cx="6" cy="6" r="5.5"/></svg>
          www.websitename.com
        </li>
      </ul>
      <address class="address">12345, Address Goes Here<br>Country Name, 123456.</address>
    </div>
  </section>

</body>
</html>
```